Anzeigengestaltung für Gas- und Wasserinstallationsunternehmen
Zielgruppe
Gas- und Wasserinstallation, wir bauen, warten und sanieren Bäder und Heizungsanlagen
Wir wollen Leute im Alter 26-45 Jahre ansprechen, mit Berufserfahrung
Aufgabenstellung
Dass wir einen Kundendienstmonteur für Öl- und Gasfeuerung suchen

```html
<!DOCTYPE html>
<html lang="de">
<head>
<meta charset="utf-8">
<title>Flammwerk24 GmbH – Stellenanzeige Kundendienstmonteur</title>
<link rel="stylesheet" href="https://fonts.googleapis.com/css2?family=Nunito+Sans:wght@400;600;700;800&display=swap">
<style>
  :root {
    --ink-light: #ffffff;
    --ember-deep: #2a0d08;
    --ember-mid: #5a1e0e;
    --ember-glow: #e8731f;
    --ember-hot: #ffc25a;
    --panel-dark: rgba(6, 22, 14, 0.82);
    --band-green: #12a55a;
    --band-teal: #14907c;
    --band-blue: #1a6fc0;
  }
  * { margin: 0; padding: 0; box-sizing: border-box; }
  html, body { width: 1200px; height: 870px; overflow: hidden; }
  body {
    font-family: "Nunito Sans", "Avenir Next", sans-serif;
    color: var(--ink-light);
    background: var(--ember-deep);
  }
  .ad { position: relative; width: 1200px; height: 870px; overflow: hidden; }

  .hero-photo {
    position: absolute; left: 0; top: 0; width: 1200px; height: 700px;
    background:
      radial-gradient(ellipse 330px 420px at 250px 430px, var(--ember-hot) 0%, var(--ember-glow) 30%, rgba(150,50,15,0.7) 60%, transparent 85%),
      radial-gradient(ellipse 500px 300px at 1050px 60px, rgba(140,60,25,0.8), transparent 80%),
      linear-gradient(180deg, var(--ember-deep) 0%, var(--ember-mid) 55%, #3a1008 100%);
  }

  .brand {
    position: absolute; left: 32px; top: 52px;
    display: flex; align-items: center; gap: 16px;
  }
  .brand-dot { width: 30px; height: 30px; border-radius: 50%; background: var(--ink-light); }
  .brand-name { font-size: 36px; font-weight: 700; letter-spacing: 0.5px; }

  .headline {
    position: absolute; left: 630px; top: 74px;
    font-size: 49px; font-weight: 800; line-height: 1.2;
  }
  .subline {
    position: absolute; left: 632px; top: 216px;
    font-size: 29px; font-weight: 700; line-height: 1.25;
  }

  .job-panel {
    position: absolute; left: 461px; top: 318px; width: 739px; height: 346px;
    background: var(--panel-dark);
    padding: 22px 24px 0 22px;
  }
  .job-title { font-size: 30px; font-weight: 800; line-height: 1.25; margin-bottom: 14px; }
  .requirements { list-style: none; font-size: 17.5px; line-height: 1.62; }
  .requirements li { position: relative; padding-left: 22px; }
  .requirements li::before {
    content: ""; position: absolute; left: 4px; top: 11px;
    width: 6px; height: 6px; border-radius: 50%; background: var(--ink-light);
  }

  .contact-band {
    position: absolute; left: 0; top: 700px; width: 1200px; height: 170px;
    background: linear-gradient(90deg, var(--band-green) 0%, var(--band-teal) 50%, var(--band-blue) 100%);
    padding: 18px 28px 0 28px;
    font-size: 19px; line-height: 1.35;
  }
  .apply-note { font-size: 18.5px; margin-bottom: 8px; }
  .contact-columns { display: flex; }
  .contact-address { width: 500px; }
  .contact-company { font-weight: 800; }
  .contact-phone { width: 360px; padding-top: 25px; }
  .contact-web { padding-top: 25px; }
</style>
</head>
<body>
<main class="ad">
  <div class="hero-photo" role="img" aria-label="Foto: Handwerker im Arbeitsoverall mit Hammer und Brenner, umgeben von Flammen vor dunklem Glutgrund"></div>

  <div class="brand">
    <span class="brand-dot"></span>
    <span class="brand-name">FLAMMWERK24 GMBH</span>
  </div>

  <h1 class="headline">Feuer und Flamme<br>für Ihren Beruf?</h1>
  <p class="subline">Wir auch!<br>Kommen Sie in unser Team.</p>

  <section class="job-panel">
    <h2 class="job-title">Wir suchen einen Kundendienstmonteur<br>für Öl- und Gasfeuerung (m/w/d):</h2>
    <ul class="requirements">
      <li>abgeschlossene Ausbildung als Gas-Installateur/in/ Monteur/in mit guten<br>Kenntnissen der Ölheizungstechnik oder ausgebildeter Heizungsmonteur</li>
      <li>mehrjährige Berufserfahrung im vorgenannten Ausbildungsfeld</li>
      <li>lösungsorientierte, selbstständige und teamorientierte Arbeitsweise</li>
      <li>Führerschein Klasse B</li>
      <li>Bewusstsein für kreative und innovative Lösungen</li>
      <li>Zukunftsorientiertes Denken und Arbeiten</li>
    </ul>
  </section>

  <footer class="contact-band">
    <p class="apply-note">Schicken Sie uns Ihre aussagekräftigen Unterlagen (Anschreiben, Lebenslauf mit Lichtbild, Zeugnissen) bitte schriftlich an:</p>
    <div class="contact-columns">
      <address class="contact-address" style="font-style:normal">
        <span class="contact-company">Flammwerk24 GmbH</span><br>
        Gesellschaft für Versorgungsanlagen mbH<br>
        Lindenhofer Str. 14 | 10437 Berlin
      </address>
      <p class="contact-phone">Tel. : +49 (0)30 41 62 - 5500<br>Fax : +49 (0)30 41 62 - 5501</p>
      <p class="contact-web">info@flammwerk24-gmbh.de<br>www.flammwerk24-gmbh.de</p>
    </div>
  </footer>
</main>
</body>
</html>
```